Letterhead for Business Law Firm

We need a letter head for our firm based on the design we have settled on and it is attached. Our clients are small and large businesses around the world, and our letterhead is used typically for formal legal purposes such as demand letters (accusing the recipient of doing bad things) or responding to demand letters. It may also be sent to regulators and other government agencies. So this needs to be tasteful, but a little edgy as well - we try to convey that we are a firm that is different - businesses and investors come to us for creative, quick advice, typically in high stress circumstances, and for our ability to work through high conflict situations, and rapid paced engagements.

Target Market(s)

Lawyers, business executives, investors, government regulators who may receive letters from this firm on behalf of its clients.

Industry/Entity Type

Business

Requirements
Must have
• The design and the firm's contact information:
• Thornwell Law Firm, P.C.
• 1876 NE 57th Ave
• Portland, OR 97213
• phone: 971 555 0147
• fax: 971 555 0182
• in what placement and how depicted (e.g. a phone icon instead of the word "phone") I leave to your creative ideas.
Nice to have
• design and information can be placed at the top, bottom and/or sides of the letter, and the design should be for a standard letter size paper - and can have a separate design for the second page.

```html
<!DOCTYPE html>
<html lang="en">
<head>
<meta charset="utf-8">
<title>Thornwell Law Firm, P.C. — Letterhead</title>
<link rel="stylesheet" href="https://fonts.googleapis.com/css2?family=Source+Sans+3:wght@400;600&display=swap">
<style>
  :root {
    --paper: #ffffff;
    --ink: #1c1718;
    --teal: #3d6676;
    --text-grey: #4d4d4f;
    --rule-grey: #c9c9c9;
    --on-teal: #ffffff;
  }
  * { margin: 0; padding: 0; box-sizing: border-box; }
  html, body { width: 933px; height: 1200px; overflow: hidden; background: var(--paper); }
  .letterhead {
    position: relative;
    width: 933px;
    height: 1200px;
    background: var(--paper);
    font-family: "Source Sans 3", "Myriad Pro", sans-serif;
    color: var(--text-grey);
  }
  .brand {
    position: absolute;
    left: 39px;
    top: 35px;
    height: 80px;
    display: flex;
    align-items: center;
    gap: 16px;
  }
  .brand-square {
    width: 56px;
    height: 80px;
    background: var(--teal);
  }
  .brand-name {
    font-weight: 400;
    font-size: 40px;
    letter-spacing: 0.22em;
    color: var(--ink);
    line-height: 1;
  }
  .address {
    position: absolute;
    left: 675px;
    top: 52px;
    height: 52px;
    padding-left: 14px;
    border-left: 1px solid var(--rule-grey);
    font-size: 17px;
    line-height: 24px;
  }
  .address-line { display: flex; align-items: center; gap: 6px; }
  .address-line--indent { padding-left: 22px; }
  .address-icon { width: 16px; height: 14px; }
  .footer-wave {
    position: absolute;
    left: 0;
    bottom: 0;
    width: 933px;
    height: 200px;
  }
  .contact {
    position: absolute;
    right: 23px;
    top: 1095px;
    list-style: none;
    color: var(--on-teal);
    font-size: 16px;
    line-height: 23.5px;
    text-align: right;
  }
  .contact-item { display: flex; justify-content: flex-end; align-items: center; gap: 6px; }
  .contact-icon { width: 13px; height: 13px; }
</style>
</head>
<body>
<main class="letterhead">
  <header>
    <div class="brand">
      <div class="brand-square" aria-hidden="true"></div>
      <span class="brand-name">THORNWELL</span>
    </div>
    <address class="address">
      <span class="address-line">
        <svg class="address-icon" viewBox="0 0 16 14" aria-hidden="true">
          <path d="M1 5 L8 1 L15 5 Z" fill="var(--teal)"/>
          <rect x="2" y="6" width="12" height="1.6" fill="var(--teal)"/>
          <rect x="2" y="9" width="12" height="1.6" fill="var(--teal)"/>
          <rect x="1" y="12" width="14" height="1.8" fill="var(--teal)"/>
        </svg>
        1876 NE 57th Ave
      </span>
      <span class="address-line address-line--indent">Portland, OR 97213</span>
    </address>
  </header>

  <footer>
    <svg class="footer-wave" viewBox="0 1000 933 200" aria-hidden="true">
      <path d="M0 1180 C 200 1196 450 1162 650 1102 C 780 1064 870 1056 933 1053 L 933 1200 L 0 1200 Z" fill="var(--teal)"/>
      <path d="M0 1140 C 150 1175 300 1181 450 1160 C 650 1130 800 1060 933 1043 L 933 1047 C 800 1068 650 1140 450 1175 C 300 1198 150 1194 0 1162 Z" fill="var(--ink)"/>
      <path d="M110 1157 C 280 1178 440 1176 560 1155 C 440 1172 280 1175 110 1157 Z" fill="var(--ink)" stroke="var(--ink)" stroke-width="1"/>
    </svg>
    <ul class="contact">
      <li class="contact-item">
        <svg class="contact-icon" viewBox="0 0 14 14" aria-hidden="true"><circle cx="7" cy="7" r="6" fill="none" stroke="var(--on-teal)" stroke-width="1.3"/><path d="M5 4 C 4 6 6 9 9 10 L 10 8.8 L 8.6 8 L 8 8.6 C 7 8 6 7 5.6 6 L 6.2 5.4 L 5.6 3.8 Z" fill="var(--on-teal)"/></svg>
        971 555 0147
      </li>
      <li class="contact-item">
        <svg class="contact-icon" viewBox="0 0 14 14" aria-hidden="true"><rect x="3.5" y="1" width="7" height="12" rx="1" fill="none" stroke="var(--on-teal)" stroke-width="1.3"/><rect x="5" y="3" width="4" height="3" fill="var(--on-teal)"/><rect x="5" y="8" width="4" height="3" fill="var(--on-teal)"/></svg>
        971 555 0182
      </li>
      <li class="contact-item">
        <svg class="contact-icon" viewBox="0 0 14 14" aria-hidden="true"><path d="M1 6 L7 2 L13 6 L13 12 L1 12 Z" fill="var(--on-teal)"/><path d="M2 6.5 L7 9.5 L12 6.5" fill="none" stroke="var(--teal)" stroke-width="1.2"/></svg>
        info@thornwelllaw.com
      </li>
      <li class="contact-item">
        <svg class="contact-icon" viewBox="0 0 14 14" aria-hidden="true"><g fill="none" stroke="var(--on-teal)" stroke-width="1.1"><circle cx="7" cy="7" r="6"/><ellipse cx="7" cy="7" rx="2.6" ry="6"/><path d="M1 7 H13 M2 4 H12 M2 10 H12"/></g></svg>
        www.thornwelllaw.com
      </li>
    </ul>
  </footer>
</main>
</body>
</html>
```